Web landing page design

- Create a Web Design (Uncoded - PSD layout only)

We need a single web page design to promote our service. This page will
acts as a landing page for users and also be utilized in social media
advertising. Please provide us with a cutting edge design. I have attached
a link for what the company is about. In essence we are a photo checking
service which reviews photos for retailers, hotels abd car dealerships to
check everything is good after a service has been performed. Whether it be
a new promotion, cleaning or just checking prices. I am looking for a
design to say that we do many photos and at a very cost effective price
(team based in Mexico)

Link: https://slidevault.example/view/qTr8nWx2LpZk4mHcYdJs/
*Deadline*
5 days
*Updates*

- The Start Here box needs to look like this:

-Start Here (heading)
-A box for email addresses to be entered
-Then a check box with "Yes, I have read and agree to the Privacy Policy
and agree to receive email marketing from Plumora88'
-A submit button

All of this information needs to be in one box please. And please feel
free to contact me if you have any questions about this.

*Target Market(s)*
Retail business, Merchandising companies, Rental property owners, Car
dealers
Updates

Please can you submit entries. I am just looking for a tidy to a presentation already created. Just needs design touches.

Target Market(s)

Ability for audience to understand concept quickly
Benefits to why to use the product stand out
Technology driven approach

Industry/Entity Type

Retail

Number of Pages Required

1 page

Colors
0792cd

Requirements
Must have
• Clean and modern design

```html
<!DOCTYPE html>
<html lang="en">
<head>
<meta charset="utf-8">
<title>Checkora – Transform retail execution</title>
<link rel="stylesheet" href="https://fonts.googleapis.com/css2?family=Lato:wght@400;700;900&family=Open+Sans:wght@400;600&display=swap">
<style>
  :root {
    --blue-deep: #1f6fa3;
    --blue-mid: #3592c6;
    --blue-light: #5cb3dd;
    --accent: #0792cd;
    --accent-bright: #2bb0f0;
    --white: #ffffff;
    --ink: #151515;
    --input-text: #333333;
    --band: rgba(22, 64, 104, 0.55);
    --rule: rgba(255, 255, 255, 0.45);
  }
  * { box-sizing: border-box; margin: 0; padding: 0; }
  html, body { width: 1200px; height: 922px; overflow: hidden; }
  body { font-family: "Open Sans", sans-serif; color: var(--white); background: var(--ink); }

  .page { position: relative; width: 1200px; height: 922px; }

  .hero-visual {
    position: absolute; left: 0; top: 0; width: 1200px; height: 840px;
    background:
      radial-gradient(ellipse at 78% 55%, rgba(70, 150, 205, 0.55), transparent 60%),
      radial-gradient(ellipse at 20% 35%, rgba(110, 190, 230, 0.45), transparent 55%),
      linear-gradient(180deg, #2f7fb2 0%, var(--blue-mid) 40%, #3a95c9 70%, var(--blue-deep) 100%);
  }

  .brand { position: absolute; left: 98px; top: 32px; width: 84px; text-align: center; }
  .brand-mark { display: block; width: 38px; height: 38px; margin: 0 auto 6px; border-radius: 50%; background: var(--white); }
  .brand-name { font-family: "Lato", sans-serif; font-weight: 700; font-size: 27px; line-height: 1; }

  .main-nav { position: absolute; top: 56px; left: 0; width: 1200px; height: 24px; }
  .main-nav a {
    position: absolute; top: 0; font-family: "Lato", sans-serif; font-weight: 700;
    font-size: 16.5px; color: var(--white); text-decoration: none; line-height: 22px;
  }
  .main-nav a.is-active { color: var(--accent-bright); }
  .nav-search { position: absolute; left: 1084px; top: 2px; }

  .headline {
    position: absolute; top: 142px; left: 0; width: 1200px; text-align: center;
    font-family: "Lato", sans-serif; font-weight: 700; font-size: 45px; line-height: 58px;
    text-shadow: 0 2px 6px rgba(0, 0, 0, 0.2);
  }

  .signup {
    position: absolute; left: 273px; top: 281px; width: 653px; height: 330px;
    border: 2px solid var(--rule);
  }
  .signup-title {
    position: absolute; top: 40px; left: 0; width: 100%; text-align: center;
    font-family: "Lato", sans-serif; font-weight: 700; font-size: 26px; letter-spacing: 0.3px;
  }
  .email-field {
    position: absolute; left: 34px; top: 92px; width: 582px; height: 53px;
    background: var(--white); display: flex; align-items: center; padding-left: 20px;
    color: var(--input-text); font-size: 15.5px;
  }
  .email-field svg { margin-right: 9px; }
  .consent { position: absolute; left: 34px; top: 170px; width: 520px; }
  .consent-box {
    position: absolute; left: 0; top: 2px; width: 16px; height: 16px;
    border: 2px solid var(--white); border-radius: 3px;
  }
  .consent-text {
    padding-left: 31px; font-family: "Lato", sans-serif; font-size: 14.5px; line-height: 24px;
  }
  .consent-text span { display: block; padding-left: 4px; }
  .submit {
    position: absolute; left: 264px; top: 243px; width: 124px; height: 50px;
    background: var(--ink); border-radius: 25px; text-align: center; line-height: 50px;
    font-family: "Lato", sans-serif; font-weight: 700; font-size: 16.5px; letter-spacing: 0.5px;
  }

  .slider-dots { position: absolute; top: 673px; left: 569px; display: flex; gap: 4px; }
  .slider-dots i {
    display: block; width: 13px; height: 13px; border-radius: 50%;
    border: 2px solid var(--white);
  }
  .slider-dots i.is-current { background: var(--white); }

  .stats {
    position: absolute; left: 0; top: 720px; width: 1200px; height: 120px; background: var(--band);
  }
  .stat { position: absolute; top: 0; width: 250px; height: 120px; text-align: center; }
  .stat + .stat { border-left: 1px solid var(--rule); }
  .stat.last { border-right: 1px solid var(--rule); }
  .stat-value {
    display: block; margin-top: 20px; font-family: "Lato", sans-serif; font-weight: 700;
    font-size: 45px; line-height: 50px;
  }
  .stat-label { display: block; margin-top: 6px; font-size: 17px; }

  .site-footer {
    position: absolute; left: 0; top: 840px; width: 1200px; height: 82px; background: var(--ink);
  }
  .copyright { position: absolute; left: 100px; top: 32px; font-size: 13px; }
  .social { position: absolute; left: 979px; top: 23px; display: flex; gap: 7px; }
  .social a {
    display: block; width: 36px; height: 36px; border-radius: 50%;
    border: 1.5px solid var(--white);
  }
</style>
</head>
<body>
<div class="page">
  <div class="hero-visual" role="img" aria-label="Blurred photo of a person in a denim shirt holding a tablet in a store, tinted blue"></div>

  <div class="brand">
    <span class="brand-mark"></span>
    <span class="brand-name">Checkora</span>
  </div>

  <nav class="main-nav">
    <a href="#" class="is-active" style="left:634px">Home</a>
    <a href="#" style="left:717px">About</a>
    <a href="#" style="left:802px">Results</a>
    <a href="#" style="left:895px">How</a>
    <a href="#" style="left:968px">Free Trials</a>
    <svg class="nav-search" width="18" height="18" viewBox="0 0 18 18" aria-label="Search">
      <circle cx="7.5" cy="7.5" r="5.5" fill="none" stroke="#fff" stroke-width="2.4"/>
      <line x1="11.5" y1="11.5" x2="16" y2="16" stroke="#fff" stroke-width="2.8" stroke-linecap="round"/>
    </svg>
  </nav>

  <h1 class="headline">Transform retail Execution<br>with a simple photo</h1>

  <form class="signup">
    <h2 class="signup-title">START HERE</h2>
    <div class="email-field">
      <svg width="17" height="13" viewBox="0 0 17 13" aria-hidden="true">
        <rect x="0" y="0" width="17" height="13" rx="1.5" fill="#333"/>
        <path d="M1 1.5 L8.5 7 L16 1.5" fill="none" stroke="#fff" stroke-width="1.3"/>
      </svg>
      Enter Email Address
    </div>
    <div class="consent">
      <span class="consent-box"></span>
      <p class="consent-text">Yes, I have read and agree to the Privacy Policy and agree to receive<span>email marketing from Plumora88</span></p>
    </div>
    <div class="submit">SUBMIT</div>
  </form>

  <div class="slider-dots"><i class="is-current"></i><i></i><i></i><i></i></div>

  <section class="stats">
    <div class="stat" style="left:71px;width:279px"><span class="stat-value">2.2M</span><span class="stat-label">Photos reviewed last year</span></div>
    <div class="stat" style="left:350px"><span class="stat-value">5P</span><span class="stat-label">From per photo reviewed</span></div>
    <div class="stat" style="left:600px"><span class="stat-value">97.2%</span><span class="stat-label">Average compliance</span></div>
    <div class="stat last" style="left:850px"><span class="stat-value">3-8%</span><span class="stat-label">Sales increase</span></div>
  </section>

  <footer class="site-footer">
    <p class="copyright">Copyrights © 2018, Checkora. All rights reserved.</p>
    <div class="social">
      <a href="#" aria-label="Social profile one"></a>
      <a href="#" aria-label="Social profile two"></a>
      <a href="#" aria-label="Social profile three"></a>
    </div>
  </footer>
</div>
</body>
</html>
```